Preisliste für Kosmetikinstitut
Zielgruppe
Ich benötige für mein Kosmetikinstitut eine Preisliste für die moderne Frau, aber auch Männer. Das Design sollte mein Logo enthalten. Farben des Designkonzepts einbauen.
A4 quer zum Falten, wie ein Heft, 1. Seite Preisliste mit logo, im Innenteil dann Anwendungen
Aufgabenstellung
Minimalistisch, ästhetisch, modern, edel
Kontaktdaten auf der Rückseite
LB Hautatelier
Lotte Brenner
Lindenhang 17
83671 Waakirchen
EMail: lotte@lb-hautatelier.de
Whatsapp: 0176 284 9017

```html
<!DOCTYPE html>
<html lang="de">
<head>
<meta charset="utf-8">
<title>LB Hautatelier – Preisliste Titelseiten</title>
<link rel="stylesheet" href="https://fonts.googleapis.com/css2?family=Questrial&family=Arimo:ital,wght@1,700&display=swap">
<style>
  :root {
    --canvas: #ffffff;
    --paper: #fcfcf4;
    --ink: #6b7774;
    --pattern-light: #eceee8;
    --pattern-mid: #c9cec9;
    --pattern-dark: #a9b0ac;
  }
  html, body {
    margin: 0;
    width: 1200px;
    height: 1200px;
    overflow: hidden;
    background: var(--canvas);
  }
  .sheet {
    position: relative;
    width: 1200px;
    height: 1200px;
  }
  .cover {
    position: absolute;
    top: 211px;
    height: 789px;
    background: var(--paper);
    box-shadow: 0 2px 10px rgba(0, 0, 0, 0.10);
  }
  .cover--plain { left: 45px; width: 539px; }
  .cover--pattern { left: 594px; width: 569px; }

  .brand {
    position: absolute;
    top: 180px;
    left: 0;
    right: 0;
    display: flex;
    align-items: center;
    justify-content: center;
    gap: 18px;
  }
  .cover--plain .brand { padding-left: 14px; }
  .cover--pattern .brand { padding-left: 6px; }
  .brand-name {
    font-family: "Questrial", sans-serif;
    font-size: 40px;
    line-height: 1;
    letter-spacing: 0.5px;
    color: var(--ink);
    white-space: nowrap;
  }
  .brand-mark {
    width: 74px;
    height: 74px;
    border: 2px solid var(--ink);
    border-radius: 50%;
    box-sizing: border-box;
  }

  .title-rule {
    position: absolute;
    top: 558px;
    width: 1px;
    height: 179px;
    background: var(--ink);
  }
  .title {
    position: absolute;
    top: 636px;
    width: 140px;
    height: 26px;
    margin-left: -70px;
    text-align: center;
    transform: rotate(-90deg);
    font-family: "Arimo", sans-serif;
    font-style: italic;
    font-weight: 700;
    font-size: 26px;
    line-height: 26px;
    color: var(--ink);
    white-space: nowrap;
  }
  .cover--plain .title-rule { left: 69px; }
  .cover--plain .title { left: 92px; }
  .cover--pattern .title-rule { left: 93px; }
  .cover--pattern .title { left: 116px; }

  .pattern-strip {
    position: absolute;
    left: 33px;
    top: 567px;
    width: 47px;
    height: 166px;
    background: linear-gradient(170deg,
      var(--pattern-light) 0%,
      var(--pattern-mid) 20%,
      var(--pattern-light) 36%,
      var(--pattern-dark) 52%,
      var(--pattern-light) 68%,
      var(--pattern-mid) 84%,
      var(--pattern-light) 100%);
  }
</style>
</head>
<body>
<main class="sheet">
  <section class="cover cover--plain">
    <div class="brand">
      <span class="brand-name">LB Hautatelier</span>
      <span class="brand-mark"></span>
    </div>
    <div class="title-rule"></div>
    <div class="title">Price List</div>
  </section>
  <section class="cover cover--pattern">
    <div class="brand">
      <span class="brand-name">LB Hautatelier</span>
      <span class="brand-mark"></span>
    </div>
    <div class="pattern-strip" role="img" aria-label="Dekoratives Linienornament aus geschwungenen, wellenförmigen Strängen"></div>
    <div class="title-rule"></div>
    <div class="title">Price List</div>
  </section>
</main>
</body>
</html>
```